Corporate Travel Technology Company needs new Business Card design

We need a new business card design to reflect our re-branded company. Our company is called tolvEn (pronounced tolvenn) and we provide Business Intelligence and mobile travel management solutions for the corporate travel industry. Our multinational customers use our solutions to manage large travel budgets and frequent travellers, as well as to save money and reduce risk. We'd like to see designs that use the blue and green palette as well as our corporate logo (attached below). The design should communicate innovation, insight, forward thinking, contemporary, trusted.

Target Market(s)

Large multinational corporates and Travel Agencies.

Industry/Entity Type

Business

Contact Information for Business Card

Rosalind Mercer
Chief Executive
tolvEn
Phone number - +61 (0)2 8134 2907
Email address - rosalind.mercer@tolven-example.com
Mobile number - +61 (0)438 516 702
www.tolven-example.com

Font styles to use
Other font styles liked:
• Please use font as close to corporate logo as possible

Colors
0255a3
0393ce
00a990
33b8a4
33a6d7
3176b5

Requirements
Must have
• Please include the words;
• Mobile Travel Management
• Accelerating Travel Business Insights
• Use corporate logo - although icon can be stylised if needed

```html
<!DOCTYPE html>
<html lang="en">
<head>
<meta charset="utf-8">
<title>tolvEn Business Card</title>
<link rel="stylesheet" href="https://fonts.googleapis.com/css2?family=Open+Sans:wght@400;600;700&display=swap">
<style>
  :root {
    --backdrop: #e9e7e3;
    --slate: #4a5c58;
    --sky: #29a8e0;
    --white: #ffffff;
    --shadow: rgba(0, 0, 0, 0.28);
  }
  * { margin: 0; padding: 0; box-sizing: border-box; }
  html, body {
    width: 1200px;
    height: 750px;
    overflow: hidden;
    background: var(--backdrop);
    font-family: "Open Sans", Arial, sans-serif;
  }
  .stage { position: relative; width: 1200px; height: 750px; }
  .card {
    position: absolute;
    top: 201px;
    width: 559px;
    height: 318px;
    overflow: hidden;
    box-shadow: 0 4px 12px var(--shadow);
  }
  .card--front { left: 28px; background: var(--slate); }
  .card--back { left: 614px; background: var(--sky); }

  .orb {
    position: absolute;
    width: 250px;
    height: 250px;
    border-radius: 50%;
  }
  .card--front .orb {
    left: 434px;
    top: 20px;
    background: var(--white);
    border: 16px solid var(--sky);
  }
  .card--back .orb {
    left: -152px;
    top: 20px;
    background: var(--slate);
    border: 16px solid var(--white);
  }

  .brand-name {
    position: absolute;
    left: 32px;
    top: 34px;
    font-size: 62px;
    font-weight: 400;
    line-height: 1;
    letter-spacing: 1px;
    color: var(--white);
  }

  .identity { position: absolute; left: 0; top: 158px; width: 430px; }
  .identity__marker {
    position: absolute; left: 2px; top: 3px;
    width: 20px; height: 34px;
    background: var(--sky);
  }
  .identity__marker::after {
    content: ""; position: absolute; left: 6px; top: 0;
    width: 14px; height: 34px; background: var(--white);
  }
  .identity__name {
    position: absolute; left: 32px; top: 0;
    font-size: 22px; font-weight: 700; letter-spacing: 0.6px;
    color: var(--white); white-space: nowrap;
  }
  .identity__role {
    position: absolute; left: 32px; top: 24px;
    font-size: 14px; color: var(--sky); white-space: nowrap;
  }
  .identity__rule {
    position: absolute; left: 145px; top: 34px;
    width: 285px; height: 1px; background: var(--sky);
  }

  .contacts { position: absolute; left: 32px; top: 227px; list-style: none; }
  .contacts__item {
    display: flex; align-items: center;
    height: 18px;
    font-size: 14.5px; color: var(--white); white-space: nowrap;
  }
  .contacts__icon { width: 12px; height: 12px; margin-right: 10px; flex: none; }

  .back-brand {
    position: absolute; left: 336px; top: 106px;
    display: flex; align-items: center; gap: 12px;
  }
  .back-brand__dot {
    width: 22px; height: 22px; border-radius: 50%; background: var(--white);
  }
  .back-brand__name {
    font-size: 40px; font-weight: 400; color: var(--white); line-height: 1;
  }

  .taglines {
    position: absolute; right: 38px; top: 234px;
    list-style: none; text-align: right;
  }
  .taglines__item {
    display: flex; justify-content: flex-end; align-items: center;
    height: 19px; font-size: 15.5px; color: var(--white); white-space: nowrap;
  }
  .taglines__item::after {
    content: ""; width: 9px; height: 9px; margin-left: 7px;
    border-radius: 50%; background: var(--slate);
  }
</style>
</head>
<body>
<main class="stage">
  <section class="card card--front" aria-label="Business card front">
    <div class="orb"></div>
    <h1 class="brand-name">tolvEn</h1>
    <div class="identity">
      <span class="identity__marker"></span>
      <p class="identity__name">ROSALIND MERCER</p>
      <p class="identity__role">Chief Executive</p>
      <span class="identity__rule"></span>
    </div>
    <ul class="contacts">
      <li class="contacts__item">
        <svg class="contacts__icon" viewBox="0 0 12 12"><rect x="3" y="0.5" width="6" height="11" rx="1" fill="none" stroke="#29a8e0" stroke-width="1.2"/><circle cx="6" cy="9.6" r="0.7" fill="#29a8e0"/></svg>
        +61 (0)438 516 702
      </li>
      <li class="contacts__item">
        <svg class="contacts__icon" viewBox="0 0 12 12"><path d="M2.5 1 L4.5 1 L5.3 3.6 L4 4.6 Q5 7.2 7.4 8 L8.4 6.7 L11 7.5 L11 9.5 Q10.5 11 9 11 Q2 10 1 3 Q1 1.5 2.5 1 Z" fill="#29a8e0"/></svg>
        +61 (0)2 8134 2907
      </li>
      <li class="contacts__item">
        <svg class="contacts__icon" viewBox="0 0 12 12" fill="none" stroke="#29a8e0" stroke-width="1"><circle cx="6" cy="6" r="5"/><ellipse cx="6" cy="6" rx="2.2" ry="5"/><line x1="1" y1="6" x2="11" y2="6"/></svg>
        www.tolven-example.com
      </li>
      <li class="contacts__item">
        <svg class="contacts__icon" viewBox="0 0 12 12" fill="none" stroke="#29a8e0" stroke-width="1.1"><rect x="0.8" y="2.5" width="10.4" height="7.5"/><polyline points="0.8,2.5 6,7 11.2,2.5"/></svg>
        rosalind.mercer@tolven-example.com
      </li>
    </ul>
  </section>

  <section class="card card--back" aria-label="Business card back">
    <div class="orb"></div>
    <div class="back-brand">
      <span class="back-brand__dot"></span>
      <span class="back-brand__name">tolvEn</span>
    </div>
    <ul class="taglines">
      <li class="taglines__item">Mobile Travel Management</li>
      <li class="taglines__item">Accelerating Travel Business Insights</li>
    </ul>
  </section>
</main>
</body>
</html>
```